Call Center In Need of Website Design

We are a call center that provides inbound and outbound calling & marketing services for eCommerce store. We would like to see a fun, creative, playful design that is simple.

Here are some sample design sites we like;
- https://www.velmoreline.com/
- https://pindrask.io/
- https://www.glimbertic.com/live-chat-software/
- https://www.zavrolin.com/

Here are some competitor sites;
- https://www.ostrevaglinks.com/
- https://www.helpkestrel.com/

I have attached website content for your use.

Target Market(s)

eCommerce

Coding

Coded - Design and coding required

Number of Pages Required

5+ page

Font styles to use
Sans Serif

Colors

Designer to choose colors to be used in the design.

Requirements
Must have
• Must have designs for the following 5 separate pages;
• 1. Home (landing)
• - This will be were the design style really needs to show.
• - Just needs to touch on key services
• - CTA
• 2. About Us
• - Basic page for about me paragraph
• 3. Services
• - List of services with icons
• - Click on service type to expand details or hover over service icon to view popup bubble with details about that service
• 4. Pricing
• - Option to bundle 1(one) digital service plan and 1(one) call center service plan
• - Bundling adds 10% monthly discount to over all price
• - Customer does NOT have to bundle
• - FAQ
• 5. Contact Us
• - Include a capture form (name, company name, email, phone, message)
• - Contact info
• - Business hours
• When customer purchases their desired plan, then they are taken to a page where they must schedule a call with an account rep.
Nice to have
• home page animations
Should not have
• All information on Home/Landing page.

```html
<!DOCTYPE html>
<html lang="en">
<head>
<meta charset="utf-8">
<title>Orbitra — Support for Small Business</title>
<link href="https://fonts.googleapis.com/css2?family=Roboto:ital,wght@0,400;0,500;0,700;1,700&family=Roboto+Condensed:wght@400;700&display=swap" rel="stylesheet">
<style>
:root{
  --teal:#4fbf9f;
  --teal-block:#66c2a8;
  --mint:#d9f0ef;
  --ink:#111111;
  --body:#333333;
  --white:#ffffff;
  --footer:#ededed;
}
*{box-sizing:border-box;margin:0;padding:0}
html,body{width:1200px;height:2795px;overflow:hidden;background:var(--white)}
body{position:relative;font-family:"Roboto Condensed",Arial,sans-serif;color:var(--ink)}
.abs{position:absolute}
.line{position:absolute;height:3px;background:var(--teal)}
.line.thin{height:1px}
.line.white{background:var(--white)}

/* hero */
.hero{position:absolute;left:0;top:0;width:1200px;height:589px;overflow:hidden;
  background:linear-gradient(100deg,#23272d 0%,#3b3f46 45%,#6b6a6e 75%,#9b9594 100%)}
.hero-shade{position:absolute;inset:0;background:linear-gradient(90deg,rgba(20,22,26,.6),rgba(20,22,26,.1))}
.brand{position:absolute;display:flex;align-items:center;gap:18px;font-family:"Roboto",sans-serif;font-weight:400;letter-spacing:6px;color:var(--teal)}
.brand .dot{width:40px;height:40px;border:3px solid var(--teal);border-radius:50%}
.nav{position:absolute;left:490px;top:46px;font-family:"Roboto",sans-serif;font-weight:700;font-size:12px;color:var(--white)}
.nav span{position:absolute;white-space:nowrap}
.account{position:absolute;left:900px;top:37px;width:138px;height:36px;background:var(--white);border:2px solid var(--teal);
  color:var(--teal);font-family:"Roboto",sans-serif;font-size:13px;font-weight:500;display:flex;align-items:center;justify-content:center}
.hero h1{position:absolute;font-family:"Roboto",sans-serif;font-style:italic;font-weight:700;font-size:64px;line-height:1;color:var(--white);white-space:nowrap}
.hero p{position:absolute;left:162px;top:385px;width:750px;font-size:14px;line-height:22px;color:var(--white)}

/* buttons */
.btn{position:absolute;background:var(--ink);color:var(--white);font-family:"Roboto",sans-serif;font-weight:700;font-size:13px;
  display:flex;align-items:center;justify-content:center;clip-path:polygon(0 0,100% 0,98% 100%,2% 100%)}

h2{font-family:"Roboto",sans-serif;font-weight:500;font-size:35px;color:var(--ink);position:absolute;white-space:nowrap}
.copy{position:absolute;font-size:12px;line-height:22px;color:var(--body)}

.photo{position:absolute}
.mint{position:absolute;background:var(--mint)}

.service-item{position:absolute}
.service-item h3{font-family:"Roboto",sans-serif;font-weight:500;font-size:22px;color:var(--teal)}
.service-item a{display:block;margin-top:2px;font-family:"Roboto",sans-serif;font-weight:700;font-size:10px;color:var(--ink);text-decoration:underline}

.faq-title{position:absolute;left:0;width:1200px;text-align:center;font-family:"Roboto",sans-serif;font-weight:500;font-size:24px;top:2108px}
.faq-sub{position:absolute;left:0;width:1200px;text-align:center;font-size:13px;line-height:19px;color:var(--body);top:2148px}
.faq{position:absolute;width:250px;text-align:center}
.faq h4{font-family:"Roboto",sans-serif;font-weight:700;font-size:12px;line-height:18px;height:38px}
.faq hr{border:0;height:1px;background:#aaa;width:170px;margin:6px auto 12px}
.faq p{font-size:12px;line-height:18px;color:var(--body)}
.arrow{position:absolute;width:16px;height:16px;border-radius:50%;background:var(--ink)}

footer{position:absolute;left:0;top:2383px;width:1200px;height:412px;background:var(--footer)}
.foot-head{position:absolute;font-family:"Roboto",sans-serif;font-weight:700;font-size:12px;color:var(--ink)}
.contact-row{position:absolute;display:flex;align-items:flex-start;gap:12px;font-size:12px;line-height:18px;color:var(--body)}
.contact-row .ico{width:22px;height:22px;border-radius:50%;background:var(--ink);flex:none;display:flex;align-items:center;justify-content:center}
.links{position:absolute;left:945px;top:2516px;list-style:none;font-size:12px;line-height:22px;color:var(--body)}
.links li::before{content:"›";margin-right:8px;color:var(--ink)}
.newsletter{position:absolute;left:162px;top:2655px;width:620px;height:52px;background:var(--ink);clip-path:polygon(0 0,100% 0,97% 100%,0 100%)}
.newsletter .label{position:absolute;left:34px;top:17px;font-family:"Roboto",sans-serif;font-weight:700;font-size:12px;color:var(--white)}
.newsletter .field{position:absolute;left:235px;top:13px;width:220px;height:32px;background:#333;color:#999;font-size:10px;padding:10px 10px}
.newsletter .submit{position:absolute;left:468px;top:12px;width:117px;height:32px;background:var(--white);font-family:"Roboto",sans-serif;font-weight:700;font-size:11px;display:flex;align-items:center;justify-content:center}
.connect{position:absolute;left:773px;top:2655px;width:265px;height:52px;background:var(--teal);clip-path:polygon(4% 0,100% 0,100% 100%,0 100%)}
.connect .label{position:absolute;left:45px;top:18px;font-family:"Roboto",sans-serif;font-weight:700;font-size:12px;color:var(--white)}
.connect .soc{position:absolute;top:16px;width:21px;height:21px;border:2px solid var(--white);border-radius:50%}
.bottom-line{position:absolute;left:162px;top:2746px;width:876px;height:1px;background:#bbb}
.legal{position:absolute;top:2763px;font-size:11px;color:var(--ink)}
</style>
</head>
<body>

<!-- hero -->
<header class="hero">
  <div class="abs" role="img" aria-label="Call center agents wearing headsets, smiling woman in the foreground" style="inset:0"></div>
  <div class="hero-shade"></div>
  <div class="line white" style="left:0;top:78px;width:30px"></div>
  <div class="line white" style="left:0;top:235px;width:55px"></div>
  <div class="line white" style="left:70px;top:310px;width:75px"></div>
  <div class="line white" style="left:105px;top:290px;width:70px;height:2px"></div>
  <div class="line white" style="left:0;top:510px;width:52px"></div>
  <div class="line white" style="left:0;top:335px;width:80px"></div>
  <div class="line white" style="left:700px;top:268px;width:80px"></div>
  <div class="line white" style="left:870px;top:205px;width:60px"></div>
  <div class="line" style="left:930px;top:240px;width:100px"></div>
  <div class="line" style="left:990px;top:178px;width:105px"></div>
  <div class="line white" style="left:1150px;top:285px;width:50px"></div>
  <div class="line white" style="left:545px;top:500px;width:95px"></div>
  <div class="line white" style="left:640px;top:500px;width:50px;height:2px"></div>
  <div class="line white" style="left:1030px;top:495px;width:100px"></div>
  <div class="line white" style="left:760px;top:0;width:65px"></div>
  <div class="line white" style="left:1170px;top:520px;width:30px"></div>

  <div class="brand" style="left:161px;top:34px;font-size:30px"><span class="dot"></span>ORBITRA</div>
  <nav class="nav">
    <span style="left:0">HOME</span>
    <span style="left:63px">ABOUT US</span>
    <span style="left:145px">SERVICES</span>
    <span style="left:225px">PRICING</span>
    <span style="left:300px">CONTACT US</span>
  </nav>
  <a class="account">Account</a>

  <h1 style="left:162px;top:222px">Orbitra is Built to</h1>
  <h1 style="left:220px;top:298px">Support Small Business</h1>
  <p>Orbitra is an omnichannel provider for customer care and back-end office support. We primarly work with eCommerce companies around the world. Our service is vital to the core operations and functionality of consumer-focused online eCommerce companies</p>
</header>

<!-- about -->
<section class="about">
  <div class="line" style="left:162px;top:664px;width:138px"></div>
  <div class="line" style="left:179px;top:690px;width:52px"></div>
  <h2 style="right:613px;top:728px">About Us</h2>
  <div class="line thin" style="left:592px;top:751px;width:94px;height:2px"></div>
  <p class="copy" style="left:186px;top:786px;width:401px;text-align:right">Orbitra is an omnichannel provider for customer care and back-end office support. We primarly work with eCommerce companies around the world. Our service is vital to the core operations and functionality of consumer-focused online eCommerce companies.Orbitra originally started out as a generalized call center support company. Based in California, the founder quickly realized that there was a lack of support for eCommerce owners that were just getting started. In 2018, Orbitra switched gears to offer professional</p>
  <a class="btn" style="left:447px;top:952px;width:140px;height:35px">Learn More</a>
  <div class="abs" style="left:689px;top:753px;width:511px;height:262px;background:var(--teal-block)"></div>
  <div class="photo" role="img" aria-label="Smiling support agent with a headset in a bright office" style="left:643px;top:691px;width:411px;height:280px;background:linear-gradient(135deg,#eceae7,#d6cfc8 55%,#9c8474)"></div>
  <div class="line" style="left:134px;top:1083px;width:93px"></div>
  <div class="line thin" style="left:0;top:1110px;width:168px"></div>
</section>

<!-- what we do -->
<section class="what">
  <div class="mint" style="left:0;top:1170px;width:538px;height:414px"></div>
  <h2 style="left:162px;top:1225px">What We Do</h2>
  <div class="line thin" style="left:356px;top:1245px;width:93px;height:2px"></div>
  <p class="copy" style="left:162px;top:1283px;width:330px">Orbitra is your personal customer service and product research team. We love eCommerce, but we love seeing business owners succeed even more! That is exactly why we have developed the processes and technology to take care of the most over looked areas in eCommerce Customer Service and Retention.<br>Let Orbitra handle your customers while you focus on growing your business.</p>
  <a class="btn" style="left:162px;top:1464px;width:138px;height:36px">Learn More</a>
  <div class="line" style="left:1000px;top:1164px;width:146px"></div>
  <div class="line thin" style="left:1062px;top:1192px;width:138px"></div>
  <div class="line" style="left:1131px;top:1216px;width:50px"></div>
  <div class="photo" role="img" aria-label="Support agent in a blue shirt with a headset presenting with open hands" style="left:640px;top:1240px;width:548px;height:450px;border-radius:6px;background:linear-gradient(160deg,#f4ebe4 0%,#e3d3c8 35%,#7f97c9 70%,#2f5ca8 100%)"></div>
</section>

<!-- services -->
<section class="services">
  <div class="line" style="left:134px;top:1701px;width:93px"></div>
  <div class="line thin" style="left:0;top:1728px;width:214px"></div>
  <div class="mint" style="left:529px;top:1692px;width:671px;height:171px"></div>
  <h2 style="right:162px;top:1738px;font-size:33px">Services</h2>
  <p class="abs" style="right:162px;top:1787px;font-family:'Roboto',sans-serif;font-weight:500;font-size:17px">We look forward to helping your business grow!</p>

  <a class="btn" style="left:162px;top:1930px;width:138px;height:34px">View More</a>

  <svg class="abs" style="left:412px;top:1900px" width="100" height="90" viewBox="0 0 100 90" role="img" aria-label="Monitor with gears icon">
    <rect x="4" y="6" width="92" height="62" rx="3" fill="none" stroke="#111" stroke-width="6"/>
    <rect x="42" y="68" width="16" height="12" fill="#111"/>
    <rect x="26" y="80" width="48" height="6" fill="#111"/>
    <circle cx="38" cy="40" r="11" fill="none" stroke="#111" stroke-width="5" stroke-dasharray="5 3"/>
    <circle cx="38" cy="40" r="4" fill="#111"/>
    <circle cx="64" cy="28" r="9" fill="none" stroke="#111" stroke-width="5" stroke-dasharray="4 3"/>
    <circle cx="64" cy="28" r="3" fill="#111"/>
  </svg>
  <div class="service-item" style="left:527px;top:1920px">
    <h3>Digital Services</h3><a>LEARN MORE</a>
  </div>

  <svg class="abs" style="left:758px;top:1900px" width="80" height="90" viewBox="0 0 80 90" role="img" aria-label="Headset icon">
    <path d="M12 50 V40 A28 28 0 0 1 68 40 V50" fill="none" stroke="#111" stroke-width="6"/>
    <rect x="4" y="42" width="16" height="26" rx="5" fill="#111"/>
    <rect x="60" y="42" width="16" height="26" rx="5" fill="#111"/>
    <path d="M68 66 Q68 80 48 82" fill="none" stroke="#111" stroke-width="4"/>
    <rect x="36" y="77" width="14" height="9" rx="4" fill="#111"/>
  </svg>
  <div class="service-item" style="left:855px;top:1920px">
    <h3>Call Center Services</h3><a>LEARN MORE</a>
  </div>
  <div class="abs" style="left:0;top:2053px;width:1200px;height:2px;background:#d8d8d8"></div>
</section>

<!-- faq -->
<section class="faqs">
  <h2 class="faq-title">Frequently Asked Questions</h2>
  <p class="faq-sub">Orbitra is your personal customer service and product research team. We love E-Commerce,<br>but we love seeing business owners succeed even more!</p>
  <div class="line" style="left:97px;top:2209px;width:93px"></div>
  <div class="line thin" style="left:0;top:2235px;width:130px"></div>
  <div class="line" style="left:1006px;top:2201px;width:93px"></div>
  <div class="line thin" style="left:1071px;top:2230px;width:129px"></div>
  <div class="line" style="left:1099px;top:2254px;width:82px"></div>
  <svg class="arrow" style="left:119px;top:2267px" viewBox="0 0 16 16"><path d="M10 4 L6 8 L10 12" stroke="#fff" stroke-width="2" fill="none"/></svg>
  <svg class="arrow" style="left:1065px;top:2267px" viewBox="0 0 16 16"><path d="M6 4 L10 8 L6 12" stroke="#fff" stroke-width="2" fill="none"/></svg>
  <div class="faq" style="left:145px;top:2228px">
    <h4>DO I HAVE TO SIGN A<br>CONTRACT?</h4><hr>
    <p>Nope. All our service plans are month-to-month answering service agreements.</p>
  </div>
  <div class="faq" style="left:471px;top:2228px">
    <h4>DO I HAVE TO PURCHASE ANY<br>HARDWARE OR EQUIPMENT?</h4><hr>
    <p>No. This is one of the major benefits of working with us. We have already invested</p>
  </div>
  <div class="faq" style="left:806px;top:2228px">
    <h4>HOW LONG DOES IT TAKE TO<br>GET STARTED?</h4><hr>
    <p>Most accounts can be set up in as little as 24 hours. More complex accounts could take longer.</p>
  </div>
</section>

<!-- footer -->
<footer></footer>
<div class="brand" style="left:162px;top:2440px;font-size:32px"><span class="dot" style="width:44px;height:44px"></span>ORBITRA</div>
<p class="copy" style="left:162px;top:2518px;width:385px;line-height:22px">Orbitra originally started out as a generalized call center support company. Based in California, the founder quickly realized that there was a lack of support for eCommerce owners that were just getting started. In 2018, Orbitra switched gears to offer professional grade call center support at a price that even start-ups could afford.</p>

<div class="foot-head" style="left:646px;top:2474px">GET IN TOUCH</div>
<div class="contact-row" style="left:646px;top:2514px">
  <span class="ico"><svg width="12" height="12" viewBox="0 0 12 12"><path d="M2 1 L4.5 1 L5.5 3.5 L4 4.5 Q5 7 7.5 8 L8.5 6.5 L11 7.5 L11 10 Q6 11 2 6 Q1 3 2 1Z" fill="#fff"/></svg></span>
  <span style="padding-top:2px">(800) 555-0142</span>
</div>
<div class="contact-row" style="left:646px;top:2548px">
  <span class="ico"><svg width="12" height="12" viewBox="0 0 12 12"><path d="M6 1 A3.5 3.5 0 0 1 9.5 4.5 C9.5 7 6 11 6 11 C6 11 2.5 7 2.5 4.5 A3.5 3.5 0 0 1 6 1Z" fill="#fff"/><circle cx="6" cy="4.5" r="1.3" fill="#111"/></svg></span>
  <span>Orbitra, Inc. 412 Larkmoor Ave.<br>Fresno, CA 93721</span>
</div>
<div class="contact-row" style="left:646px;top:2595px">
  <span class="ico"><svg width="12" height="10" viewBox="0 0 12 10"><rect x="1" y="1" width="10" height="8" fill="none" stroke="#fff" stroke-width="1.4"/><path d="M1 1 L6 6 L11 1" fill="none" stroke="#fff" stroke-width="1.4"/></svg></span>
  <span style="padding-top:2px">info@orbitra.com</span>
</div>

<div class="foot-head" style="left:945px;top:2474px">COMAPNY LINKS</div>
<ul class="links">
  <li>Home</li><li>About Us</li><li>Services</li><li>Pricing</li><li>Contact Us</li>
</ul>

<div class="newsletter">
  <span class="label">Sign-Up to Our Newsletter :</span>
  <span class="field">Enter Your E-mail</span>
  <span class="submit">SIGN UP</span>
</div>
<div class="connect">
  <span class="label">Connect Via :</span>
  <span class="soc" style="left:138px"></span>
  <span class="soc" style="left:165px"></span>
  <span class="soc" style="left:192px"></span>
  <span class="soc" style="left:219px"></span>
</div>

<div class="bottom-line"></div>
<p class="legal" style="left:162px">© Copyright 2018 Orbitra. All Rights Reserved.</p>
<p class="legal" style="right:162px">Terms and Conditons</p>

</body>
</html>
```